Letterhead and business card design

We have recently had a logo designed by brandnestly. now we need a corporate identity with business card and lettehead design.

Target Market(s)

law firms corporates

Industry/Entity Type

Business

Requirements
Should not have
• cheesy detecive stuff like magnifying glasses etxcc

```html
<!DOCTYPE html>
<html lang="en">
<head>
<meta charset="utf-8">
<title>Letterhead Footer</title>
<link href="https://fonts.googleapis.com/css2?family=Didact+Gothic&display=swap" rel="stylesheet">
<style>
  :root {
    --backdrop: #dcdcdc;
    --paper: #f3f3f3;
    --ink: #666666;
    --ink-soft: #7a7a7a;
    --rule: #8a8a8a;
  }
  * { margin: 0; padding: 0; box-sizing: border-box; }
  html, body {
    width: 1200px; height: 778px; overflow: hidden;
    background: var(--backdrop);
    font-family: "Didact Gothic", "Century Gothic", sans-serif;
    color: var(--ink);
  }
  .letterhead {
    position: absolute; left: 60px; top: 0;
    width: 1080px; height: 738px;
    background: var(--paper);
    box-shadow: 0 4px 14px rgba(0,0,0,0.12);
  }
  .footer {
    position: absolute; left: 0; right: 0; bottom: 70px;
    display: flex; flex-direction: column; align-items: center;
  }
  .contact-row {
    display: flex; align-items: center;
    font-size: 19px; line-height: 1.3;
  }
  .contact-block { padding: 0 28px; }
  .address { text-align: right; }
  .divider { width: 1px; height: 40px; background: var(--rule); }
  .contact-line { display: flex; align-items: center; gap: 8px; }
  .contact-line svg { width: 15px; height: 15px; fill: var(--ink); flex: none; }
  .phones .contact-line { font-size: 17px; }
  .disclaimer {
    margin-top: 22px; max-width: 740px;
    text-align: center; font-size: 13px; line-height: 1.35;
    color: var(--ink-soft);
  }
</style>
</head>
<body>
  <div class="letterhead">
    <footer class="footer">
      <div class="contact-row">
        <div class="contact-block address">
          <div>PO Box 318, Harbour Lane</div>
          <div>Kestrel Bay, New Zealand</div>
        </div>
        <span class="divider"></span>
        <div class="contact-block online">
          <div class="contact-line">
            <svg viewBox="0 0 16 16" aria-hidden="true"><path d="M1 3h14v10H1z M2 4.2v.6l6 4 6-4v-.6l-6 4z" fill-rule="evenodd"/></svg>
            <span>mara@northlineinquiry.co.nz</span>
          </div>
          <div class="contact-line">
            <svg viewBox="0 0 16 16" aria-hidden="true"><path d="M8 1a7 7 0 1 0 0 14A7 7 0 0 0 8 1zm0 1.3c.8 0 1.7 1.5 2 3.7H6c.3-2.2 1.2-3.7 2-3.7zM5.7 7.3h4.6a12 12 0 0 1 0 1.4H5.7a12 12 0 0 1 0-1.4zM2.4 7.3h2a14 14 0 0 0 0 1.4h-2a5.8 5.8 0 0 1 0-1.4zm9.2 0h2a5.8 5.8 0 0 1 0 1.4h-2a14 14 0 0 0 0-1.4zM6 10h4c-.3 2.2-1.2 3.7-2 3.7S6.3 12.2 6 10z"/></svg>
            <span>www.northlineinquiry.co.nz</span>
          </div>
        </div>
        <span class="divider"></span>
        <div class="contact-block phones">
          <div class="contact-line">
            <svg viewBox="0 0 16 16" aria-hidden="true"><path d="M2 4h12v10H2z M4 1h6v3H4z M4 6h8v2H4z M4 10h2v2H4z M7 10h2v2H7z M10 10h2v2h-2z" fill-rule="evenodd"/></svg>
            <span>+64 9 555 0142</span>
          </div>
          <div class="contact-line">
            <svg viewBox="0 0 16 16" aria-hidden="true"><path d="M4 1h8v14H4z M5.3 2.5v9h5.4v-9z M7.2 12.6h1.6v1.2H7.2z" fill-rule="evenodd"/></svg>
            <span>+64 9 555 0187</span>
          </div>
        </div>
      </div>
      <p class="disclaimer">Government Licenced Private Investigators (licence number 480372). Harlow and Vance Investigations Limited have no more authority than that of an ordinary private citizen to require a reply to this correspondence.</p>
    </footer>
  </div>
</body>
</html>
```